RESIDENTIAL CONSTRUCTION

We are a company that specializes in building custom residential homes, the design should also emphasize that quality and service is our priority.

Industry/Entity Type

Construction Company

Contact Information for Business Card

Contact Person: Marcus Lindqvist
Company Address: 273 West Alder Ave San Jose , Ca 95380
Phone Number : 408-731-2946
Email Address: Stoneridgehomes517@mailvista.net

Font styles to use
Sans Serif

Colors
ec1f27

Requirements
Must have
• CSLB # 7362015
Nice to have
• needs to have same color as logo i uploaded, we will be printing these on a clear plastic card.

```html
<!DOCTYPE html>
<html lang="en">
<head>
<meta charset="utf-8">
<title>Stoneridge General Builders – Business Card</title>
<link rel="stylesheet" href="https://fonts.googleapis.com/css2?family=Roboto:wght@400;500;700&display=swap">
<style>
  :root {
    --backdrop: #e6e4e1;
    --card: #fbfbfa;
    --brand-red: #a81c2e;
    --ink: #3a3a3a;
    --rule: #555555;
  }
  * { margin: 0; padding: 0; box-sizing: border-box; }
  html, body {
    width: 1200px;
    height: 802px;
    overflow: hidden;
    background: var(--backdrop);
    font-family: "Roboto", Arial, sans-serif;
  }
  .canvas {
    position: relative;
    width: 1200px;
    height: 802px;
  }
  .business-card {
    position: absolute;
    left: 100px;
    top: 115px;
    width: 1000px;
    height: 572px;
    background: var(--card);
    box-shadow: 0 6px 24px rgba(0,0,0,0.12);
  }
  .brand {
    position: absolute;
    left: 390px;
    top: 88px;
    display: flex;
    align-items: center;
    gap: 16px;
  }
  .brand-square {
    width: 44px;
    height: 44px;
    background: var(--brand-red);
  }
  .brand-name {
    font-size: 34px;
    font-weight: 700;
    color: var(--brand-red);
    letter-spacing: 0.5px;
    text-transform: uppercase;
  }
  .name-row {
    position: absolute;
    left: 60px;
    right: 60px;
    top: 200px;
    display: flex;
    align-items: center;
    gap: 20px;
  }
  .name-rule {
    flex: 1;
    height: 1px;
    background: var(--rule);
  }
  .name-rule--left { flex: 1.35; }
  .contact-name {
    font-size: 28px;
    font-weight: 500;
    color: var(--brand-red);
    letter-spacing: 1px;
    text-transform: uppercase;
    white-space: nowrap;
  }
  .contact-details {
    position: absolute;
    left: 60px;
    top: 240px;
    font-size: 21px;
    line-height: 30px;
    color: var(--ink);
  }
  .office-details {
    position: absolute;
    right: 60px;
    top: 400px;
    font-size: 21px;
    line-height: 30px;
    color: var(--ink);
    text-align: right;
    letter-spacing: 0.5px;
  }
</style>
</head>
<body>
<div class="canvas">
  <section class="business-card">
    <div class="brand">
      <span class="brand-square"></span>
      <span class="brand-name">Stoneridge General Builders</span>
    </div>

    <div class="name-row">
      <span class="name-rule name-rule--left"></span>
      <span class="contact-name">Marcus Lindqvist</span>
      <span class="name-rule"></span>
    </div>

    <div class="contact-details">
      <p class="phone">P. 408-731-2946</p>
      <p class="email">Stoneridgehomes517@mailvista.net</p>
      <p class="website">www.stoneridgebuilders.net</p>
    </div>

    <div class="office-details">
      <p class="address">273 West Alder Ave San</p>
      <p class="address">Jose, Ca 95380</p>
      <p class="license">CSLB # 7362015</p>
    </div>
  </section>
</div>
</body>
</html>
```